Events Company Needs Website Revamp

Tallwood Expos is an events company that specializes in organizing and marketing large scale consumer and trade events globally.

The new web design should provide easy classification of the events, and allow visitors to find and access the details page within 2 clicks.

There are no strict guidelines on the color theme. It just has to blend naturally with the corporate logo.
Updates

The company logo is uploaded (pdf & ai)

I came across this design which I like very much. Elegant and corporate with nice modern fonttype.

Layout wise, neat and clear. 

Please see how you can emulate the design further. Particularly, highlighting the 2 event arms (Trade/Consumer) clearly.

Target Market(s)

Consumer looking for upcoming events, B2C companies looking to participate, B2B companies looking to connect with other companies

Industry/Entity Type

It Company

Requirements
Must have
• The new design should help to achieve the following objectives:
1) Visitors should be able to easily identify and access the 2 different types of events (i.e. Trade Events and Consumer Events).
2) Visitors should be able to easily find events that interest them (e.g. filter by date, trade or consumer, category [i.e. beauty, retail, F&B, construction, etc.]).
3) Visitors should be able to access an event’s details page within 2 clicks from any page.

Main navigation to include the following links:
- About Us
- Calendar
- Consumer Events
- Trade Events
- Contact Us

Design for Three (3) pages required:
A. Homepage
- Clear differentiation and easy access to the 2 different types of events (trade and consumer)
- Featured area to showcase latest 4-5 events
- Quick way to access events calendar
- Clear call-to-action for newsletter signup
- Social media sharing widgets/buttons
- A section for latest news and press releases
- A section for featured testimonials

B. Events Listing Page
- List of links to all events
- Logos and/or photos of events
- Filter / tags to find events in a specific category (e.g. food, electronics, building & construction, etc.)

C. Events Details Page
- Photo strip to showcase event photos / brochure
- A section with event details (Date, Venue, Event Description, etc.)
- Call-to-action button to visit event website
- Call-to-action button to contact event sales team
- E.g. http://vantly-demo.com/user/brightfoxhk/brightfox-monday-2011 but with the photo strip permanently extended and of a shorter height. Event details and call-to-action buttons should also be easily seen

```html
<!DOCTYPE html>
<html lang="en">
<head>
<meta charset="utf-8">
<title>Tallwood Expos</title>
<link rel="stylesheet" href="https://fonts.googleapis.com/css2?family=Oswald:wght@400;500&family=Arimo:ital,wght@0,400;0,700;1,400&display=swap">
<style>
:root{
  --purple:#6e0d7b;
  --purple-dark:#560862;
  --purple-light:#86179a;
  --orange:#f58220;
  --ink:#111;
  --grey:#777;
  --ice:#eaf2fb;
  --hatch:#e2e2e2;
}
*{box-sizing:border-box;margin:0;padding:0}
html,body{width:969px;height:1200px;overflow:hidden;background:#fff}
body{position:relative;font-family:"Arimo",Arial,sans-serif;color:var(--grey)}
.abs{position:absolute}
.display{font-family:"Oswald","Arial Narrow",sans-serif;font-weight:500;color:var(--ink)}

/* header */
.masthead{left:0;top:0;width:969px;height:222px;background:linear-gradient(180deg,var(--purple-light) 0%,var(--purple) 45%,var(--purple-dark) 100%)}
.masthead-edge{left:0;top:212px}
.brand{left:50px;top:-76px;width:160px;height:160px;border-radius:50%;background:#fff;border:3px solid #8a2a9a;display:flex;align-items:flex-end;justify-content:center;padding-bottom:44px}
.brand-name{font-family:"Oswald",sans-serif;font-size:15px;color:#555;letter-spacing:.3px}
.nav{left:346px;top:0;display:flex;height:56px}
.nav a{font-family:"Oswald",sans-serif;font-weight:500;font-size:21px;color:#fff;text-decoration:none;padding:0 12px;height:56px;border-left:1px solid rgba(255,255,255,.08);text-shadow:0 1px 2px rgba(0,0,0,.4);display:block;white-space:nowrap}
.nav a span{display:block;line-height:22px;margin-top:25px}
.nav a.current{background:rgba(0,0,0,.12)}

/* event arms */
.globe{left:352px;top:175px;width:292px;height:292px;border-radius:50%;background:radial-gradient(circle at 45% 40%,#fafafa 0%,#dcdcdc 55%,#a9a9a9 100%);box-shadow:0 22px 24px -14px rgba(0,0,0,.35)}
.arm-title{font-size:44px;top:230px;line-height:58px;white-space:nowrap}
.arm-text{top:300px;font-size:13px;line-height:20.5px;color:var(--grey);white-space:nowrap}
.btn{top:384px;width:95px;height:33px;border:1px solid #c8c8c8;background:linear-gradient(#fbfbfb,#e3e3e3);font-family:"Oswald",sans-serif;font-weight:500;font-size:14px;color:#333;display:flex;align-items:center;justify-content:center}
.hatch{height:8px;background:repeating-linear-gradient(-45deg,var(--hatch) 0 2px,transparent 2px 4px)}

/* featured */
.featured{left:48px;top:498px;width:886px;height:61px;background:var(--ice)}
.featured-label{left:0;top:0;width:179px;height:61px;background:linear-gradient(#f2f2f2,#d9d9d9);border-right:1px solid #cfcfcf;display:flex;align-items:center;padding-left:24px;gap:14px;font-size:14px;color:#3b2048;white-space:nowrap}
.featured-logo{top:16px;width:30px;height:30px;border-radius:4px;background:#8d8d8d}

/* columns */
.col-title{font-size:20px;top:648px;white-space:nowrap}
.news-thumb{left:48px;width:47px;height:47px;border:1px solid #dde6f0;background:#fff;padding:6px}
.news-thumb div{width:100%;height:100%;background:#e48a2a;border-radius:3px}
.news-head{left:108px;font-family:"Oswald",sans-serif;font-weight:500;font-size:15px;color:#888;line-height:20px}
.news-text{left:108px;font-size:13px;line-height:20px;white-space:nowrap}
.more{font-size:13px;color:var(--purple);white-space:nowrap}
.quote-mark{left:372px;font-family:"Oswald",sans-serif;font-weight:500;font-size:44px;color:#9a9a9a;line-height:40px}
.quote-text{left:405px;font-size:13px;line-height:20px;white-space:nowrap}
.quote-by{right:334px;font-style:italic;font-size:13px;color:#333;white-space:nowrap}

/* calendar */
.calendar{left:668px;top:655px;width:265px;height:268px;background:#fff;overflow:hidden}
.cal-head{height:32px;background:#0a0a0a;display:flex;align-items:center;padding:0 8px 0 17px;font-size:13px;color:#fff;gap:20px}
.cal-select{width:186px;height:16px;background:#fff;border:1px solid #888;font-size:12px;color:#000;padding-left:3px;line-height:14px;position:relative}
.cal-select::after{content:"";position:absolute;right:0;top:0;width:24px;height:14px;background:var(--purple)}
.cal-grid{display:grid;grid-template-columns:87px 87px 89px;grid-auto-rows:58px;gap:1px;background:#cfd8e2;padding-top:1px}
.cal-month{background:var(--ice);padding:7px 10px;font-family:"Oswald",sans-serif;font-weight:500;font-size:20px;color:#8a8a8a;line-height:26px}
.cal-month svg{display:block;margin-top:2px}
.tooltip{left:770px;top:803px;width:158px;height:25px;background:#4a0750;color:#fff;font-size:12px;display:flex;align-items:center;justify-content:center;white-space:nowrap}

/* footer */
.footer-edge{left:0;top:995px}
.f-title{font-family:"Oswald",sans-serif;font-weight:500;font-size:14px;color:var(--ink);top:1057px}
.f-text{font-size:12px;color:#666;line-height:14.5px;white-space:nowrap}
.social{left:436px;top:1083px;display:flex;gap:9px}
.social span{width:26px;height:26px;border-radius:50%;background:#4a0750;display:flex;align-items:center;justify-content:center}
.subscribe{left:616px;top:1101px;display:flex}
.subscribe-input{width:170px;height:22px;border:1px solid #ccc;font-style:italic;font-size:11px;color:#888;padding:4px 7px}
.subscribe-btn{width:52px;height:22px;background:linear-gradient(#f4f4f4,#dcdcdc);border:1px solid #ccc;border-left:0;font-size:10px;font-weight:700;color:#222;display:flex;align-items:center;justify-content:center}
.to-top{left:890px;top:1107px;text-align:center;font-size:12px;color:#111;width:30px}
</style>
</head>
<body>

<header>
  <div class="abs masthead"></div>
  <svg class="abs masthead-edge" width="969" height="14" viewBox="0 0 969 14" aria-hidden="true">
    <path d="M0 6 Q485 16 969 6 L969 8 Q485 18 0 8 Z" fill="var(--orange)"/>
  </svg>
  <div class="abs brand"><span class="brand-name">Tallwood Expos</span></div>
  <nav class="abs nav">
    <a class="current"><span>About Us</span></a>
    <a><span>Calendar</span></a>
    <a><span>Trade Events</span></a>
    <a><span>Consumer Events</span></a>
    <a><span>Contact Us</span></a>
  </nav>
</header>

<main>
  <div class="abs globe" role="img" aria-label="3D globe built from white cubes carrying event logos"></div>

  <h1 class="abs display arm-title" style="left:50px">Trade Events</h1>
  <p class="abs arm-text" style="left:50px">Lorem ipsum dolor sit amet, consectetur<br>adipiscing elit. Curabitur ac lorem eu sem<br>congue pharetra. Vestibulum eget lacus nibh.</p>
  <div class="abs btn" style="left:48px">VIew More</div>
  <div class="abs hatch" style="left:48px;top:436px;width:306px"></div>

  <h1 class="abs display arm-title" style="right:35px">Consumer Events</h1>
  <p class="abs arm-text" style="right:33px;text-align:right">Lorem ipsum dolor sit amet, consectetur<br>adipiscing elit. Curabitur ac lorem eu sem<br>congue pharetra. Vestibulum eget lacus nibh.</p>
  <div class="abs btn" style="left:840px">VIew More</div>
  <div class="abs hatch" style="left:629px;top:436px;width:305px"></div>

  <section class="abs featured">
    <div class="abs featured-label">Featured Events
      <svg width="34" height="24" viewBox="0 0 34 24" aria-hidden="true">
        <path d="M13 0 L0 12 L13 24 Z M20 0 L33 12 L20 24 Z" fill="#4a0750"/>
      </svg>
    </div>
    <div class="abs featured-logo" style="left:239px"></div>
    <div class="abs featured-logo" style="left:327px;background:#333"></div>
    <div class="abs featured-logo" style="left:410px;border-radius:50%;background:#c9c9c9"></div>
    <div class="abs featured-logo" style="left:487px;width:54px;background:#9a9a9a"></div>
    <div class="abs featured-logo" style="left:590px;width:56px;height:24px;top:18px;background:#c0141c"></div>
    <div class="abs featured-logo" style="left:707px"></div>
    <div class="abs featured-logo" style="left:795px;background:#333"></div>
  </section>
  <div class="abs hatch" style="left:48px;top:603px;width:886px"></div>

  <h2 class="abs display col-title" style="left:48px">Latest News</h2>
  <div class="abs news-thumb" style="top:708px"><div></div></div>
  <div class="abs news-head" style="top:705px">Lorem Ipsum</div>
  <div class="abs hatch" style="left:108px;top:729px;width:220px;height:6px"></div>
  <p class="abs news-text" style="top:740px">Lorem ipsum dolor sit amet, vehicula<br>integer tortor libero, mollis sed...</p>
  <a class="abs more" style="left:108px;top:787px">Read More</a>

  <div class="abs news-thumb" style="top:827px"><div></div></div>
  <div class="abs news-head" style="top:824px">Lorem Ipsum</div>
  <div class="abs hatch" style="left:108px;top:848px;width:220px;height:6px"></div>
  <p class="abs news-text" style="top:859px">Lorem ipsum dolor sit amet, vehicula<br>integer tortor libero, mollis sed...</p>
  <a class="abs more" style="left:108px;top:906px">Read More</a>

  <h2 class="abs display col-title" style="left:369px">Testimonials</h2>
  <div class="abs quote-mark" style="top:705px">&ldquo;</div>
  <p class="abs quote-text" style="top:704px">Lorem ipsum dolor sit amet, consectetur<br>adipiscing elit. Curabitur ac lorem eu<br>sem congue pharetra.</p>
  <div class="abs quote-by" style="top:767px">Mark Ellison</div>
  <div class="abs quote-mark" style="top:803px">&ldquo;</div>
  <p class="abs quote-text" style="top:802px">Lorem ipsum dolor sit amet, consectetur<br>adipiscing elit. Curabitur ac lorem eu<br>sem congue pharetra.</p>
  <div class="abs quote-by" style="top:866px">Mark Ellison</div>
  <a class="abs more" style="left:405px;top:906px">Read More</a>

  <section class="abs calendar">
    <div class="cal-head">Year <div class="cal-select">2012</div></div>
    <div class="cal-grid">
      <div class="cal-month">JAN</div>
      <div class="cal-month">FEB</div>
      <div class="cal-month">MAR</div>
      <div class="cal-month">APR
        <svg width="12" height="8" viewBox="0 0 12 8" aria-hidden="true"><g fill="#555"><circle cx="4" cy="2" r="2"/><path d="M0 8 Q4 3 8 8Z"/><circle cx="8.5" cy="2" r="2"/><path d="M5 8 Q8.5 3 12 8Z"/></g></svg>
      </div>
      <div class="cal-month">MAY
        <svg width="46" height="8" viewBox="0 0 46 8" aria-hidden="true"><g fill="#555"><circle cx="4" cy="2" r="2"/><path d="M0 8 Q4 3 8 8Z"/><circle cx="8.5" cy="2" r="2"/><path d="M5 8 Q8.5 3 12 8Z"/><circle cx="20" cy="2" r="2"/><path d="M16 8 Q20 3 24 8Z"/><circle cx="24.5" cy="2" r="2"/><path d="M21 8 Q24.5 3 28 8Z"/><rect x="34" y="3" width="2" height="5"/><rect x="37" y="1" width="2" height="7"/><rect x="40" y="4" width="2" height="4"/><rect x="43" y="2" width="2" height="6"/></g></svg>
      </div>
      <div class="cal-month">JUN</div>
      <div class="cal-month">JUL</div>
      <div class="cal-month">AUG</div>
      <div class="cal-month">SEP</div>
      <div class="cal-month">OCT</div>
      <div class="cal-month">NOV</div>
      <div class="cal-month">DEC
        <svg width="12" height="8" viewBox="0 0 12 8" aria-hidden="true"><g fill="#555"><circle cx="4" cy="2" r="2"/><path d="M0 8 Q4 3 8 8Z"/><circle cx="8.5" cy="2" r="2"/><path d="M5 8 Q8.5 3 12 8Z"/></g></svg>
      </div>
    </div>
  </section>
  <div class="abs tooltip">Little Steps Expo 2012</div>
</main>

<footer>
  <svg class="abs footer-edge" width="969" height="16" viewBox="0 0 969 16" aria-hidden="true">
    <path d="M120 10 Q485 0 850 10 Z" fill="#4a0750"/>
    <rect x="0" y="10" width="969" height="3" fill="var(--orange)"/>
  </svg>

  <div class="abs f-title" style="left:49px">Copyright</div>
  <p class="abs f-text" style="left:49px;top:1081px">© Tallwood Expos 2009-2010. All Rights Reserved.</p>
  <p class="abs f-text" style="left:49px;top:1116px">• Tel: (65) 6200-1180 or (65) 6200-1181<br>• Fax: (65) 6200-1190<br>• hello@tallwoodexpos.sg</p>

  <div class="abs f-title" style="left:436px">Connect wit Us</div>
  <div class="abs social">
    <span></span>
    <span></span>
    <span><svg width="14" height="14" viewBox="0 0 14 14" aria-hidden="true"><circle cx="2.5" cy="11.5" r="2" fill="#fff"/><path d="M1 6 A7 7 0 0 1 8 13 M1 1 A12 12 0 0 1 13 13" stroke="#fff" stroke-width="2" fill="none"/></svg></span>
    <span><svg width="14" height="10" viewBox="0 0 14 10" aria-hidden="true"><rect x="0.5" y="0.5" width="13" height="9" fill="#fff"/><path d="M0.5 0.5 L7 6 L13.5 0.5" stroke="#4a0750" fill="none"/></svg></span>
  </div>

  <div class="abs f-title" style="left:616px">Subscribe</div>
  <p class="abs f-text" style="left:616px;top:1077px">Get free event updates &amp; specials!</p>
  <div class="abs subscribe">
    <div class="subscribe-input">Enter Email</div>
    <div class="subscribe-btn">SUBMIT</div>
  </div>

  <div class="abs to-top">
    <svg width="26" height="44" viewBox="0 0 26 44" aria-hidden="true"><path d="M13 0 L26 15 L19 15 L19 44 L13 38 L7 44 L7 15 L0 15 Z" fill="var(--orange)"/></svg>
    <div>Top</div>
  </div>
</footer>

</body>
</html>
```